Parkway Rubber Crew

I need a wrap designed for a box truck. The company is a mobile tire shop. It’s a tire shop on wheels, that comes anywhere you are to service your tires.

```html
<!DOCTYPE html>
<html lang="en">
<head>
<meta charset="utf-8">
<title>Parkway Rubber Crew – Box Truck Wrap</title>
<link href="https://fonts.googleapis.com/css2?family=Audiowide&family=Lato:wght@700&display=swap" rel="stylesheet">
<style>
  :root {
    --page-bg: #e2e2e2;
    --panel-black: #05080b;
    --panel-glow: #2d5a74;
    --brand-blue: #1fa3e6;
    --band-light: #3fbaf2;
    --band-dark: #0b86cc;
    --text-white: #ffffff;
    --chrome-light: #f4f6f8;
    --chrome-mid: #9aa3aa;
    --chrome-dark: #4a5158;
    --tire-dark: #111417;
    --tire-mid: #3c444b;
  }
  * { margin: 0; padding: 0; box-sizing: border-box; }
  html, body {
    width: 1068px; height: 1200px; overflow: hidden;
    background: var(--page-bg);
  }
  .wrap-panel {
    position: absolute; left: 44px; top: 402px;
    width: 980px; height: 396px;
    background:
      radial-gradient(ellipse 260px 90px at 380px 30px, rgba(90,150,185,.55), transparent 70%),
      radial-gradient(ellipse 420px 160px at 330px 250px, rgba(45,90,116,.45), transparent 75%),
      radial-gradient(ellipse 200px 160px at 830px 250px, rgba(45,90,116,.5), transparent 75%),
      var(--panel-black);
    box-shadow: 0 6px 14px rgba(0,0,0,.35);
    font-family: "Audiowide", sans-serif;
    color: var(--text-white);
    overflow: hidden;
  }
  .kicker {
    position: absolute; left: 35px; top: 28px;
    font-size: 13.5px; letter-spacing: .3px;
  }
  .headline {
    position: absolute; left: 33px; top: 44px;
    font-size: 74px; line-height: 1; letter-spacing: 1px;
    background: linear-gradient(180deg, var(--chrome-light) 0%, var(--chrome-mid) 48%, var(--chrome-dark) 52%, var(--chrome-light) 100%);
    -webkit-background-clip: text; background-clip: text;
    color: transparent;
  }
  .subhead {
    position: absolute; right: 348px; top: 112px;
    font-size: 40px; line-height: 1; color: var(--brand-blue);
  }
  .services { position: absolute; left: 33px; top: 170px; }
  .service {
    position: absolute; display: flex; align-items: center; gap: 10px;
    font-size: 11.5px; line-height: 1.25; white-space: nowrap;
  }
  .service-icon { width: 27px; height: 27px; flex: none; }
  .divider {
    position: absolute; width: 2px; background: var(--text-white);
  }
  .phone {
    position: absolute; left: 32px; top: 277px;
    display: flex; align-items: center; gap: 8px;
    font-size: 40px; line-height: 1;
  }
  .phone-icon { width: 42px; height: 42px; }
  .phone-divider { left: 379px; top: 279px; height: 40px; }
  .partner-strip {
    position: absolute; left: 402px; top: 280px;
    width: 250px; height: 33px; background: var(--text-white);
    display: grid; grid-template-columns: repeat(4, 1fr); gap: 3px; padding: 4px 5px;
  }
  .partner-badge { border-radius: 2px; }
  .tire-stack {
    position: absolute; left: 690px; top: 91px;
    width: 268px; height: 246px;
    background: radial-gradient(ellipse at 45% 40%, var(--tire-mid), var(--tire-dark) 70%);
    border-radius: 40px;
  }
  .company-mark {
    position: absolute; left: 790px; top: 42px;
    display: flex; align-items: center; gap: 7px;
    font-size: 15px; color: var(--brand-blue);
  }
  .company-mark .dot {
    width: 16px; height: 16px; border-radius: 50%; background: var(--brand-blue);
  }
  .slogan-band {
    position: absolute; left: 0; bottom: 0; width: 100%; height: 51px;
    background: linear-gradient(180deg, var(--band-light), var(--band-dark));
    display: flex; align-items: center; justify-content: center;
    font-size: 26px; letter-spacing: .5px;
    text-shadow: 0 2px 2px rgba(0,0,0,.45);
  }
</style>
</head>
<body>
<section class="wrap-panel">
  <p class="kicker">THIS TRUCK CARRIES ALL THE EQUIPMENT NEEDED TO GET YOU BACK ON THE ROAD !</p>
  <h1 class="headline">TREADS 2 GO</h1>
  <p class="subhead">MOBILE TIRES</p>

  <div class="company-mark"><span class="dot"></span><span>Parkway Rubber Crew</span></div>

  <div class="services">
    <div class="service" style="left:0;top:0;">
      <svg class="service-icon" viewBox="0 0 28 28"><circle cx="14" cy="14" r="12.5" fill="none" stroke="#fff" stroke-width="1.3"/><circle cx="14" cy="14" r="6" fill="none" stroke="#fff" stroke-width="1.3"/><circle cx="14" cy="14" r="2" fill="#fff"/></svg>
      <span>TIRE MOUNTING<br>&amp; INSTALLATION</span>
    </div>
    <div class="service" style="left:0;top:50px;">
      <svg class="service-icon" viewBox="0 0 28 28"><circle cx="14" cy="14" r="12.5" fill="none" stroke="#fff" stroke-width="1.3"/><path d="M9 19l7-7m-2-3l5 5" stroke="#fff" stroke-width="1.5" fill="none"/></svg>
      <span>TIRE REPAIRS</span>
    </div>
    <div class="divider" style="left:165px;top:-4px;height:78px;"></div>
    <div class="service" style="left:196px;top:0;">
      <svg class="service-icon" viewBox="0 0 28 28"><circle cx="14" cy="14" r="12.5" fill="none" stroke="#fff" stroke-width="1.3"/><circle cx="14" cy="14" r="7" fill="none" stroke="#fff" stroke-width="1.3"/><path d="M14 7v14M7 14h14" stroke="#fff" stroke-width="1"/></svg>
      <span>NEW &amp; USED TIRES</span>
    </div>
    <div class="service" style="left:196px;top:50px;">
      <svg class="service-icon" viewBox="0 0 28 28"><circle cx="14" cy="14" r="12.5" fill="none" stroke="#fff" stroke-width="1.3"/><path d="M8 17h12v3H8zM10 17l2-4h4l2 4" stroke="#fff" stroke-width="1.2" fill="none"/></svg>
      <span>EMERGENCY<br>ROADSIDE SERVICE</span>
    </div>
    <div class="divider" style="left:388px;top:-4px;height:78px;"></div>
    <div class="service" style="left:419px;top:0;">
      <svg class="service-icon" viewBox="0 0 28 28"><circle cx="14" cy="14" r="12.5" fill="none" stroke="#fff" stroke-width="1.3"/><path d="M9 20V11l5-3 5 3v9z" stroke="#fff" stroke-width="1.2" fill="none"/></svg>
      <span>COMPETITIVE<br>WHOLESALE PRICING</span>
    </div>
    <div class="service" style="left:419px;top:50px;">
      <svg class="service-icon" viewBox="0 0 28 28"><circle cx="14" cy="14" r="12.5" fill="none" stroke="#fff" stroke-width="1.3"/><rect x="8" y="11" width="6" height="6" fill="none" stroke="#fff" stroke-width="1.2"/><rect x="15" y="9" width="5" height="10" fill="none" stroke="#fff" stroke-width="1.2"/></svg>
      <span>LOW PROFILE TIRES<br>&amp; CUSTOM WHEELS</span>
    </div>
  </div>

  <div class="phone">
    <svg class="phone-icon" viewBox="0 0 42 42"><circle cx="21" cy="21" r="19" fill="none" stroke="#fff" stroke-width="2.5"/><path d="M14 12c-2 2-1 7 4 12s10 6 12 4l1-2-4-3-2 2c-2-1-5-4-6-6l2-2-3-4z" fill="#fff"/></svg>
    <span>0123456789</span>
  </div>
  <div class="divider phone-divider"></div>
  <div class="partner-strip" aria-label="Partner tire brands">
    <span class="partner-badge" style="background:#e8292a"></span>
    <span class="partner-badge" style="background:#222"></span>
    <span class="partner-badge" style="background:#1a4fa0"></span>
    <span class="partner-badge" style="background:#d8242a"></span>
    <span class="partner-badge" style="background:#1d5fb4"></span>
    <span class="partner-badge" style="background:#2b4aa0"></span>
    <span class="partner-badge" style="background:#e07a12"></span>
    <span class="partner-badge" style="background:#e9a21a"></span>
  </div>

  <div class="tire-stack" role="img" aria-label="Stack of black tires with silver alloy wheels"></div>

  <div class="slogan-band">“DON’T WAIT AT A TIRE SHOP, WE’LL COME TO YOU!”</div>
</section>
</body>
</html>
```